Classic and neutral book cover design

We are looking for a classic and neutral book cover design to be used as the template for a series of books to be published. We are hence looking for a template that will allow us to easily change the title name for all books in this series.
The use of very few colours (black and white is welcome) and few design elements is a big bonus. As a source of inspiration we would like to ask you to view the very simple and
If you think you have a cool idea that can add a twist to the formal classic look don't hesitate. Go for it !
Work will be done for a 30 year old Sweden based cultural non-profit called VĂ©ru (www.verufoundation.example). We work with the publishing and supporting of post-modern art and literature addressing contemporary topics but are also involved in assisting projects of cultural preservation.
Target Market(s)
The audience is expected to have some form of interest in culture but could range from hobbyist readers to tenure track scholars
Industry/Entity Type
Non-Profit
Requirements
Must have
- General:
- Classic and neutral feel
- Preferably very simple and few shapes
- usage of few colours (black and white is welcome)
Information to be displayed on the cover is:
- Author
- Title
- type of work e.g. play/novel (optional)
- publishing house (in this case "Veru Publishing")
Nice to have
- ideas to prevent it from become boring are of course welcome
Should not have
- - too many colours

```html
<!DOCTYPE html>
<html lang="en">
<head>
<meta charset="utf-8">
<title>Book Cover – Veru Publishing</title>
<link rel="stylesheet" href="https://fonts.googleapis.com/css2?family=Tinos&display=swap">
<style>
  :root {
    --cover-green: #1c7a22;
    --cover-black: #000000;
    --cover-white: #ffffff;
    --type-serif: "Tinos", "Times New Roman", serif;
  }
  html, body {
    margin: 0;
    padding: 0;
    overflow: hidden;
    background: var(--cover-white);
  }
  .cover {
    position: relative;
    width: 915px;
    height: 1200px;
    overflow: hidden;
    background: var(--cover-white);
    font-family: var(--type-serif);
  }
  .cover__artwork {
    position: absolute;
    left: 0;
    top: 0;
    width: 845px;
    height: 1200px;
    background: linear-gradient(180deg,
      var(--cover-green) 0%,
      var(--cover-green) 30%,
      #0e3d11 55%,
      var(--cover-black) 75%,
      var(--cover-black) 100%);
  }
  .cover__page {
    position: absolute;
    left: 0;
    top: 0;
  }
  .cover__author {
    position: absolute;
    left: 0;
    width: 865px;
    top: 28px;
    text-align: center;
    font-size: 78px;
    line-height: 1;
    color: var(--cover-white);
    margin: 0;
    font-weight: 400;
  }
  .cover__title {
    position: absolute;
    left: 400px;
    width: 440px;
    top: 605px;
    text-align: center;
    font-size: 112px;
    line-height: 146px;
    color: var(--cover-black);
    margin: 0;
    font-weight: 400;
  }
  .cover__publisher {
    position: absolute;
    left: 400px;
    top: 1105px;
    font-size: 50px;
    line-height: 1;
    color: var(--cover-white);
    margin: 0;
  }
</style>
</head>
<body>
  <main class="cover">
    <div class="cover__artwork" role="img" aria-label="Illustration of a woman with dark hair and a bow, eyes closed, reading an open book held in her hand, in green, black and white"></div>
    <svg class="cover__page" width="915" height="1200" viewBox="0 0 915 1200" aria-hidden="true">
      <polygon points="372,468 560,512 845,585 845,925 455,962 398,900" fill="var(--cover-white)"/>
    </svg>
    <h2 class="cover__author">Author of Book</h2>
    <h1 class="cover__title">Title of<br>Book</h1>
    <p class="cover__publisher">Veru Publishing</p>
  </main>
</body>
</html>
```